Healthy Meal Delivery Website needs a new face lift

Hi there,

The current website i have is super old and outdated.

I would like a beautiful modern site that has all the same content as the previous except with a a new, modern and trustworthy feel.

The current website is http://www.larkibite.ca/

Target Market(s)

Diet Meal delivery, weight loss, healthy meal delivery

Industry/Entity Type

Food Service

Number of Pages Required

5+ page

Font styles to use
Sans Serif

Requirements
Must have
• Modern & Clean
Should not have
• Anything outdated or cheesy

```html
<!DOCTYPE html>
<html lang="en">
<head>
<meta charset="utf-8">
<title>Larkibite – Diet Meal Delivery</title>
<link href="https://fonts.googleapis.com/css2?family=Roboto+Slab:wght@400;700&family=Open+Sans:wght@400;600;700&family=Montserrat:wght@600&display=swap" rel="stylesheet">
<style>
:root{
  --blue:#29abe2;
  --blue-dark:#1e94c7;
  --ink:#333;
  --text:#555;
  --muted:#777;
  --light:#f4f4f4;
  --footer:#2c2c2c;
  --white:#fff;
}
*{box-sizing:border-box;margin:0;padding:0}
html,body{width:1200px;height:3015px;overflow:hidden}
body{font-family:"Open Sans",Arial,sans-serif;color:var(--text);background:var(--white);position:relative}
section,header,footer{position:absolute;left:0;width:1200px}

/* header */
.site-header{top:0;height:120px;background:var(--white);border-top:4px solid var(--blue)}
.brand{position:absolute;left:86px;top:22px;display:flex;align-items:center;gap:12px}
.brand-dot{width:26px;height:26px;border-radius:50%;background:var(--blue)}
.brand-name{font-family:"Roboto Slab",Georgia,serif;font-weight:700;font-size:40px;color:var(--blue);letter-spacing:1px}
.topbar{position:absolute;right:86px;top:22px;display:flex;gap:26px;font-size:13px;color:#444;text-transform:uppercase;align-items:center}
.topbar span{display:flex;align-items:center;gap:7px}
.main-nav{position:absolute;left:352px;top:66px;width:848px;height:52px;background:var(--blue);clip-path:polygon(26px 0,100% 0,100% 100%,0 100%)}
.main-nav ul{list-style:none;display:flex;height:100%;align-items:center;padding-left:24px}
.main-nav li{padding:0 23px;color:var(--white);font-size:13.5px;text-transform:uppercase;height:100%;display:flex;align-items:center;border-left:1px solid rgba(255,255,255,.18);transform:skewX(-20deg)}
.main-nav li:first-child{border-left:none}
.main-nav li span{transform:skewX(20deg)}

/* hero */
.hero{top:120px;height:513px;background:radial-gradient(ellipse at 35% 40%,#8a4a22 0%,#4a2412 35%,#1b100a 75%)}
.hero-text{position:absolute;top:205px;width:100%;text-align:center}
.hero-kicker{font-family:"Roboto Slab",Georgia,serif;color:var(--blue);font-size:30px}
.hero-title{font-family:"Roboto Slab",Georgia,serif;color:var(--white);font-size:40px;font-weight:400;margin-top:10px}
.btn-pill{display:inline-block;margin-top:26px;background:var(--blue);color:var(--white);font-family:"Roboto Slab",Georgia,serif;font-size:17px;padding:13px 30px;border-radius:30px}

/* about */
.about{top:633px;height:507px;background:linear-gradient(90deg,#e6edf1 0%,#eef2f4 50%,#e9edef 100%)}
.about-photo{position:absolute;left:543px;top:0;width:657px;height:507px;background:radial-gradient(ellipse at 50% 55%,#e9d5c6 0%,#e4e7e9 45%,#eef1f3 80%)}
.about-copy{position:absolute;left:86px;top:72px;width:460px}
.about-copy h3{font-family:"Roboto Slab",Georgia,serif;font-weight:400;font-size:25px;color:var(--ink)}
.about-copy h2{font-family:"Roboto Slab",Georgia,serif;font-weight:400;font-size:31px;color:var(--blue);margin-top:6px}
.about-copy p{font-size:12.5px;line-height:26px;color:#666;margin-top:22px}
.about-copy p+p{margin-top:22px}

/* features */
.features{top:1140px;height:344px;background:var(--white)}
.feature{position:absolute;top:70px;width:240px;margin-left:-120px;text-align:center}
.feature svg{display:block;margin:0 auto}
.feature h4{font-family:"Roboto Slab",Georgia,serif;font-weight:400;color:var(--blue);font-size:18px;margin-top:12px;letter-spacing:.5px}
.feature p{font-size:12.5px;color:#666;line-height:23px;margin-top:2px}

/* program */
.program{top:1484px;height:552px;background:var(--light)}
.section-title{font-family:"Roboto Slab",Georgia,serif;font-weight:400;color:var(--blue);font-size:32px;text-align:center;position:absolute;top:28px;width:100%}
.section-sub{position:absolute;top:76px;width:100%;text-align:center;font-size:12.5px;color:#666}
.card{position:absolute;top:110px;width:330px}
.card-photo{height:211px}
.card h4{font-family:"Roboto Slab",Georgia,serif;font-weight:400;color:var(--blue);font-size:17px;margin-top:22px}
.card p{font-size:12.5px;line-height:27px;color:#555;margin-top:10px}
.btn-box{display:inline-block;margin-top:16px;background:var(--blue);color:var(--white);font-size:12px;padding:9px 16px;text-transform:uppercase}

/* delivery */
.delivery{top:2036px;height:442px;background:linear-gradient(90deg,#c9b9a8 0%,#d8cfc6 30%,#e4e2df 55%,#eceaea 100%)}
.delivery-photo{position:absolute;left:0;top:0;width:600px;height:442px;background:radial-gradient(ellipse at 40% 60%,#8fbf3a 0%,#b9a070 35%,rgba(210,200,190,0) 75%)}
.delivery h2{position:absolute;left:615px;top:48px;font-family:"Roboto Slab",Georgia,serif;font-weight:400;color:var(--blue);font-size:31px}
.accordion{position:absolute;left:617px;top:114px;width:484px}
.acc-item{height:40px;border:2px solid var(--white);color:var(--white);font-family:"Roboto Slab",Georgia,serif;font-size:14px;display:flex;align-items:center;justify-content:space-between;padding:0 14px;margin-bottom:12px;background:rgba(255,255,255,.08)}
.acc-item .sign{width:16px;height:16px;background:var(--white);color:#999;font-size:14px;line-height:16px;text-align:center;font-family:Arial,sans-serif;font-weight:700}
.acc-body{color:var(--white);font-size:12px;line-height:25px;padding:6px 12px 14px 16px}

/* testimonial */
.testimonial{top:2478px;height:288px;background:var(--blue)}
.t-body{position:absolute;left:183px;top:72px;width:560px;color:var(--white)}
.quote-open{position:absolute;left:-19px;top:-16px;font-family:Georgia,serif;font-size:40px;line-height:1}
.quote{font-size:12px;line-height:25px}
.quote-close{display:block;height:26px;padding-left:384px;font-family:Georgia,serif;font-size:40px;line-height:40px;overflow:visible}
.t-name{font-weight:700;font-size:14px;text-transform:uppercase;margin-top:4px}
.t-date{font-size:12.5px;margin-top:2px}
.avatar{position:absolute;left:781px;top:48px;width:194px;height:194px;border-radius:50%;border:5px solid var(--white);background:radial-gradient(circle at 50% 45%,#d9b39a 0%,#8c6a55 60%,#5a4536 100%)}
.slide-arrow{position:absolute;top:106px}

/* footer */
.site-footer{top:2766px;height:249px;background:var(--footer);color:var(--white)}
.footer-brand{position:absolute;left:170px;top:50px;display:flex;align-items:center;gap:12px}
.footer-brand .brand-name{font-size:46px}
.footer-col h5{font-family:"Montserrat",Arial,sans-serif;font-weight:600;font-size:15px;letter-spacing:1px;text-transform:uppercase}
.links{position:absolute;left:506px;top:30px}
.links ul{list-style:none;display:grid;grid-template-columns:125px 125px;row-gap:13px;margin-top:20px;font-size:12.5px}
.newsletter{position:absolute;left:764px;top:30px;width:337px}
.newsletter p{font-size:12.5px;margin-top:20px}
.signup{margin-top:14px;display:flex;height:44px}
.signup .field{flex:1;background:var(--white);color:#666;font-size:12.5px;display:flex;align-items:center;padding-left:18px}
.signup .send{width:44px;background:var(--blue);display:flex;align-items:center;justify-content:center}
.footer-rule{position:absolute;left:86px;right:86px;top:189px;border-top:1px solid #444}
.copyright{position:absolute;top:212px;width:100%;text-align:center;font-size:12.5px}
</style>
</head>
<body>

<header class="site-header">
  <div class="brand"><span class="brand-dot"></span><span class="brand-name">Larkibite</span></div>
  <div class="topbar">
    <span><svg width="12" height="12" viewBox="0 0 24 24"><path fill="#555" d="M6.6 10.8a15 15 0 0 0 6.6 6.6l2.2-2.2a1 1 0 0 1 1-.25 11 11 0 0 0 3.6.6 1 1 0 0 1 1 1V20a1 1 0 0 1-1 1A17 17 0 0 1 3 4a1 1 0 0 1 1-1h3.5a1 1 0 0 1 1 1 11 11 0 0 0 .6 3.6 1 1 0 0 1-.25 1z"/></svg>Call Us : 416-555-0142</span>
    <span><svg width="11" height="12" viewBox="0 0 20 22"><rect x="2" y="9" width="16" height="12" fill="#555"/><path d="M5 9V6a5 5 0 0 1 10 0v3" stroke="#555" stroke-width="2.5" fill="none"/></svg>Sign Up</span>
    <span>|</span>
    <span><svg width="11" height="12" viewBox="0 0 20 22"><circle cx="10" cy="6" r="5" fill="#555"/><path d="M0 22a10 9 0 0 1 20 0z" fill="#555"/></svg>Customer Login</span>
  </div>
  <nav class="main-nav">
    <ul>
      <li><span>Home</span></li><li><span>How It Works</span></li><li><span>Pricing</span></li><li><span>Sample Menu</span></li><li><span>Celebrity</span></li><li><span>F.A.Q.</span></li><li><span>Contact</span></li>
    </ul>
  </nav>
</header>

<section class="hero" role="img" aria-label="Close-up photo of a wrap with rice, salsa and lime on a dark plate">
  <div class="hero-text">
    <div class="hero-kicker">Great Tasting Diet Meal Delivery</div>
    <h1 class="hero-title">Diet Meal Delivery Toronto &amp; Canada wide</h1>
    <span class="btn-pill">Click Here For More Info</span>
  </div>
</section>

<section class="about">
  <div class="about-photo" role="img" aria-label="Photo of a smiling woman in sportswear juggling a banana, oranges and an apple against a white brick wall"></div>
  <div class="about-copy">
    <h3>Fresh Diet Gourmet</h3>
    <h2>Meals Delivered By Larkibite</h2>
    <p>Fresh diet meal delivery Toronto and Canada wide is our signature fresh gourmet diet meal delivery program designed for healthy living &amp; weight loss management. Diet meal delivery Toronto has a creative gourmet menu that uses exotic flavors &amp; ingredients to enhance your dining experience.</p>
    <p>The Larkibite Plan is based on 30% lean protein and the rest fruits and vegetables with a dash of Heart Healthy monounsaturated fats. Once these levels are reached and maintained, the body enters a state of hormonal balance which produces many positive effects, such as stable insulin and glucagon levels</p>
  </div>
</section>

<section class="features">
  <div class="feature" style="left:211px">
    <svg width="140" height="150" viewBox="0 0 140 150"><path d="M10 70a60 60 0 1 1 120 0" fill="none" stroke="#29abe2" stroke-width="10"/><path d="M15 80a55 55 0 0 0 110 0" fill="none" stroke="#e6f4fb" stroke-width="2"/><circle cx="70" cy="72" r="20" fill="none" stroke="#29abe2" stroke-width="3"/><circle cx="70" cy="72" r="9" fill="none" stroke="#29abe2" stroke-width="3"/><path d="M70 72l22-22m0 0v-8m0 8h8" stroke="#29abe2" stroke-width="3" fill="none"/><path d="M60 132h20l-10 12z" fill="#29abe2"/></svg>
    <h4>BENEFITS</h4><p>Fresh diet meal delivery daily</p>
  </div>
  <div class="feature" style="left:474px">
    <svg width="140" height="150" viewBox="0 0 140 150"><path d="M10 70a60 60 0 1 1 120 0" fill="none" stroke="#29abe2" stroke-width="10"/><g fill="#29abe2"><rect x="50" y="58" width="6" height="6"/><rect x="60" y="58" width="32" height="6"/><rect x="50" y="70" width="6" height="6"/><rect x="60" y="70" width="32" height="6"/><rect x="50" y="82" width="6" height="6"/><rect x="60" y="82" width="32" height="6"/></g><path d="M60 132h20l-10 12z" fill="#29abe2"/></svg>
    <h4>MENU</h4><p>Inspired fresh gourmet Larkibite<br>Diet meals</p>
  </div>
  <div class="feature" style="left:734px">
    <svg width="140" height="150" viewBox="0 0 140 150"><path d="M10 70a60 60 0 1 1 120 0" fill="none" stroke="#29abe2" stroke-width="10"/><g stroke="#29abe2" stroke-width="3"><line x1="70" y1="48" x2="70" y2="96"/><line x1="49" y1="60" x2="91" y2="84"/><line x1="49" y1="84" x2="91" y2="60"/></g><g fill="#29abe2"><circle cx="70" cy="72" r="8"/><circle cx="70" cy="48" r="5"/><circle cx="70" cy="96" r="5"/><circle cx="49" cy="60" r="5"/><circle cx="91" cy="84" r="5"/><circle cx="49" cy="84" r="5"/><circle cx="91" cy="60" r="5"/></g><path d="M60 132h20l-10 12z" fill="#29abe2"/></svg>
    <h4>VARIETY</h4><p>60 Day Menu Rotation</p>
  </div>
  <div class="feature" style="left:997px">
    <svg width="140" height="150" viewBox="0 0 140 150"><path d="M10 70a60 60 0 1 1 120 0" fill="none" stroke="#29abe2" stroke-width="10"/><g fill="none" stroke="#29abe2" stroke-width="3"><rect x="44" y="62" width="34" height="22"/><path d="M78 68h12l8 8v8H78"/><circle cx="55" cy="88" r="5"/><circle cx="88" cy="88" r="5"/><circle cx="70" cy="56" r="9"/><path d="M70 51v5h4"/></g><path d="M60 132h20l-10 12z" fill="#29abe2"/></svg>
    <h4>DELIVERY</h4><p>Fresh diet meal delivery daily<br>Toronto &amp; Canada wide</p>
  </div>
</section>

<section class="program">
  <h2 class="section-title">Program Details</h2>
  <p class="section-sub">Your daily temperature controlled cooler will have all of your meals so you won't need &nbsp;to supplement with any additional</p>
  <article class="card" style="left:86px">
    <div class="card-photo" role="img" aria-label="Photo of halved vegetable wraps" style="background:linear-gradient(135deg,#c9b48a,#8e9a52 50%,#d7c6a2)"></div>
    <h4>Pause Your Program Anytime</h4>
    <p>You are welcome to pause and restart your meal program at anytime. Our customers lead busy lives, therefore if you need to post-pone a delivery let us know</p>
    <span class="btn-box">Read More</span>
  </article>
  <article class="card" style="left:436px">
    <div class="card-photo" role="img" aria-label="Photo of a smiling woman in a white sweater at a kitchen table" style="background:linear-gradient(135deg,#cfd6da,#e8ddd3 50%,#b9c2c6)"></div>
    <h4>Customized For You</h4>
    <p>You are welcome to pause and restart your meal program at anytime. Our customers lead busy lives, therefore if you need to post-pone a delivery let us know</p>
    <span class="btn-box">Read More</span>
  </article>
  <article class="card" style="left:784px">
    <div class="card-photo" role="img" aria-label="Photo of roasted glazed chicken pieces" style="background:radial-gradient(ellipse at 50% 55%,#c04a1a,#7a2a10 55%,#2a1208)"></div>
    <h4>Enjoy Our Gourmet Menu</h4>
    <p>You are welcome to pause and restart your meal program at anytime. Our customers lead busy lives, therefore if you need to post-pone a delivery let us know</p>
    <span class="btn-box">Read More</span>
  </article>
</section>

<section class="delivery">
  <div class="delivery-photo" role="img" aria-label="Photo of a green apple, a salad bowl and a measuring tape on a wooden table"></div>
  <h2>Delivery System</h2>
  <div class="accordion">
    <div class="acc-item" style="margin-bottom:0">What's In Your Bag?<span class="sign">&minus;</span></div>
    <div class="acc-body">Your daily temperature controlled cooler will have all of your meals so you won't need to supplement with any additional snacks or produce during the day.</div>
    <div class="acc-item">Your Daily Menu<span class="sign">+</span></div>
    <div class="acc-item">Recyclable Containers<span class="sign">+</span></div>
    <div class="acc-item">Returning Your Cooler<span class="sign">+</span></div>
  </div>
</section>

<section class="testimonial">
  <svg class="slide-arrow" style="left:54px" width="20" height="80" viewBox="0 0 20 80"><path d="M18 0L2 40l16 40" fill="none" stroke="rgba(255,255,255,.5)" stroke-width="2"/></svg>
  <div class="t-body">
    <span class="quote-open">&ldquo;</span>
    <p class="quote">Sed ut perspiciatis unde omnis iste natus error sit voluptatem accusantium doloremque laudantium, totam rem aperiam, eaque ipsa quae ab illo inventore veritatis et quasi architecto beatae vitae dicta sunt explicabo. Nemo enim ipsam voluptatem quia voluptas sit aspernatur aut odit aut fugit, sed quia consequuntur magni dolores eos qui ratione voluptatem sequi nesciunt.</p>
    <span class="quote-close">&rdquo;</span>
    <div class="t-name">Maren Doyle</div>
    <div class="t-date">Posted On 07 May 2018</div>
  </div>
  <div class="avatar" role="img" aria-label="Portrait photo of the reviewer"></div>
  <svg class="slide-arrow" style="left:1126px" width="20" height="80" viewBox="0 0 20 80"><path d="M2 0l16 40L2 80" fill="none" stroke="rgba(255,255,255,.5)" stroke-width="2"/></svg>
</section>

<footer class="site-footer">
  <div class="footer-brand"><span class="brand-dot"></span><span class="brand-name">Larkibite</span></div>
  <div class="footer-col links">
    <h5>Quick Links</h5>
    <ul><li>Home</li><li>Celebrity</li><li>How It Works</li><li>F.A.Q.</li><li>Pricing</li><li>Contact</li><li>Sample Menu</li></ul>
  </div>
  <div class="footer-col newsletter">
    <h5>Newsletter</h5>
    <p>Sed ut perspiciatis unde omnis iste natus error sit</p>
    <div class="signup"><span class="field">Enter Your Email Id</span><span class="send"><svg width="18" height="18" viewBox="0 0 24 24"><path d="M2 11L22 2l-7 20-4-8z" fill="#fff"/></svg></span></div>
  </div>
  <div class="footer-rule"></div>
  <p class="copyright">&copy; Copy Right -2018 Larkibite Meals All rights reserved.</p>
</footer>

</body>
</html>
```